Brightway Haul & Upkeep Services, are a company that offers a 'one stop shop' pre-move clean up a

I have already selected a logo which I would like on the front of the business cards along with phone numbers, web address and email which are:
0487650392
www.brightwayhaul.com.au
brightwayhaulandupkeep@mailbox.example

On the back of the card I would like to list some of the types of service we offer (clean - move - repairs/maintenance) which are:
CLEAN - windows, gutters, solar panels, driveways/paths, carpets.
MOVE - Small/medium size house/office moves, large item pick-up & delivery, yard clean-up and removal.
General maintenance and repairs.

I would like the blue logo on a gray background.

Thanks

```html
<!DOCTYPE html>
<html lang="en">
<head>
<meta charset="utf-8">
<title>Brightway Haul &amp; Upkeep Services – Business Cards</title>
<link rel="stylesheet" href="https://fonts.googleapis.com/css2?family=Open+Sans:wght@400;600;700;800&family=Jost:wght@400&display=swap">
<style>
  :root {
    --backdrop: #ecebe8;
    --card-light: #eeeff0;
    --card-dark: #c8c9cb;
    --brand-blue: #2e72bf;
    --ink: #231f20;
    --ink-soft: #3a3a3c;
    --rule: #b5b6b8;
  }
  * { box-sizing: border-box; margin: 0; padding: 0; }
  html, body {
    width: 1200px; height: 788px; overflow: hidden;
    background: var(--backdrop);
  }
  .sheet {
    width: 1200px; height: 788px;
    display: flex; align-items: center; justify-content: center; gap: 40px;
  }
  .card {
    width: 540px; height: 330px;
    background: linear-gradient(160deg, var(--card-light) 0%, #dcdddf 55%, var(--card-dark) 100%);
    box-shadow: 0 6px 18px rgba(0,0,0,.18);
    position: relative;
    font-family: "Open Sans", sans-serif;
    color: var(--ink);
  }
  .brand-name {
    font-family: "Open Sans", sans-serif;
    font-weight: 800;
    color: var(--brand-blue);
    font-size: 34px;
    line-height: 1.1;
    text-align: center;
    text-transform: uppercase;
  }
  /* Front */
  .card--front .brand-name {
    position: absolute; left: 40px; right: 40px; top: 62px;
  }
  .contact {
    position: absolute; left: 0; right: 0; bottom: 52px;
    display: flex; align-items: center; justify-content: center; gap: 26px;
    font-family: "Jost", sans-serif; font-size: 14px; color: var(--ink-soft);
  }
  .contact__divider { width: 1px; height: 54px; background: var(--rule); }
  .contact__list { display: flex; flex-direction: column; gap: 12px; }
  .contact__item { display: flex; align-items: center; gap: 8px; }
  .contact__icon { width: 14px; height: 14px; flex: none; }
  /* Back */
  .card--back .brand-name {
    position: absolute; left: 40px; right: 40px; top: 40px;
  }
  .services {
    position: absolute; left: 0; right: 0; top: 170px; text-align: center;
  }
  .services__title {
    font-weight: 600; font-size: 20px; letter-spacing: 7px;
    color: var(--brand-blue); margin-bottom: 10px;
  }
  .services__list { list-style: none; font-weight: 600; font-size: 18px; line-height: 1.45; }
  .services__list li span + span { margin-left: 22px; }
</style>
</head>
<body>
<main class="sheet">
  <section class="card card--front" aria-label="Card front">
    <h1 class="brand-name">Brightway Haul &amp; Upkeep Services</h1>
    <div class="contact">
      <div class="contact__item">
        <svg class="contact__icon" viewBox="0 0 16 16" aria-hidden="true"><circle cx="8" cy="8" r="7.5" fill="none" stroke="#2e72bf"/><path d="M5.2 4.2l1.5 1.6-.8 1a5 5 0 0 0 2.3 2.3l1-.8 1.6 1.5-.9 1.1C7 10.5 5 8.5 4.2 5.1z" fill="#2e72bf"/></svg>
        <span>0487650392</span>
      </div>
      <span class="contact__divider"></span>
      <div class="contact__list">
        <div class="contact__item">
          <svg class="contact__icon" viewBox="0 0 16 16" aria-hidden="true"><rect x="1.5" y="3.5" width="13" height="9" rx="1.5" fill="#2e72bf"/><path d="M2 4.5l6 4.5 6-4.5" fill="none" stroke="#fff" stroke-width="1.2"/></svg>
          <span>brightwayhaulandupkeep@mailbox.example</span>
        </div>
        <div class="contact__item">
          <svg class="contact__icon" viewBox="0 0 16 16" aria-hidden="true"><circle cx="8" cy="8" r="6.5" fill="#2e72bf"/><path d="M1.5 8h13M8 1.5c-3 3.5-3 9.5 0 13M8 1.5c3 3.5 3 9.5 0 13" fill="none" stroke="#fff" stroke-width=".9"/></svg>
          <span>www.brightwayhaul.com.au</span>
        </div>
      </div>
    </div>
  </section>

  <section class="card card--back" aria-label="Card back">
    <h2 class="brand-name">Brightway Haul &amp; Upkeep Services</h2>
    <div class="services">
      <p class="services__title">Services we offer</p>
      <ul class="services__list">
        <li><span>• Clean</span><span>• Move</span></li>
        <li>• General maintenance and repairs.</li>
      </ul>
    </div>
  </section>
</main>
</body>
</html>
```